Italian restaurant needs new site

Need to make our website better.

Must have reservation module

Must be able to sell wine tasting tours and wine pairing tours and intégrate with dunmo desk

Blog

Social media

Wandervane ranking and last review.
Updates

Number of Pages Required

1 page

Font styles to use
Serif

Requirements
Must have
• Reservation module
• Marketplace to buy wine pairings and gift certificates
• Wandervane review
• Kindlepost posts
• All info from old site

```html
<!DOCTYPE html>
<html lang="en">
<head>
<meta charset="utf-8">
<title>Serata Bistro — Italian Cuisine &amp; Wine Bar</title>
<link rel="stylesheet" href="https://fonts.googleapis.com/css2?family=Playfair+Display:wght@400;700&family=Noto+Serif:wght@400;700&display=swap">
<style>
  :root {
    --ink-white: #ffffff;
    --soft-white: #e8e2dc;
    --wine: #a3202a;
    --accent-red: #d4202b;
    --bar: #0b0a0a;
    --shade-dark: #140d0c;
    --shade-warm: #6b2a1c;
    --shade-amber: #a5623a;
  }
  * { box-sizing: border-box; margin: 0; padding: 0; }
  html, body {
    width: 1200px; height: 706px; overflow: hidden;
    background: var(--shade-dark);
  }
  .hero {
    position: relative; width: 1200px; height: 706px; overflow: hidden;
    font-family: "Noto Serif", Georgia, serif; color: var(--ink-white);
  }
  .hero-photo {
    position: absolute; inset: 0;
    background:
      radial-gradient(ellipse 420px 320px at 820px 260px, rgba(165,98,58,.55), transparent 70%),
      radial-gradient(ellipse 360px 260px at 260px 420px, rgba(120,48,30,.5), transparent 70%),
      linear-gradient(180deg, #2a1612 0%, var(--shade-warm) 45%, #2c1410 80%, var(--shade-dark) 100%);
  }
  .hero-photo::after {
    content: ""; position: absolute; inset: 0;
    background: linear-gradient(90deg, rgba(10,6,6,.55) 0%, rgba(10,6,6,.15) 40%, rgba(10,6,6,.2) 70%, rgba(10,6,6,.6) 100%);
  }
  .social-links {
    position: absolute; top: 25px; left: 14px;
    display: flex; align-items: center; gap: 9px;
    font-size: 10px; font-weight: 700; letter-spacing: .2px;
  }
  .social-links span { color: var(--ink-white); }
  .social-links svg { display: block; }
  .brand-banner {
    position: absolute; left: 514px; top: 0; width: 172px; height: 181px;
  }
  .brand-banner svg { position: absolute; inset: 0; }
  .brand-name {
    position: absolute; left: 0; right: 0; top: 70px; text-align: center;
    font-family: "Playfair Display", Georgia, serif; font-size: 23px; font-weight: 400;
    line-height: 1; color: var(--wine); white-space: nowrap;
  }
  .menu-toggle {
    position: absolute; left: 1138px; top: 12px; width: 49px; height: 41px;
    border: 1px solid var(--ink-white); display: flex; flex-direction: column;
    justify-content: center; align-items: center; gap: 6px;
  }
  .menu-toggle i { display: block; width: 27px; height: 2px; background: var(--ink-white); }
  .hero-copy {
    position: absolute; left: 0; right: 0; top: 308px; text-align: center;
  }
  .hero-title {
    font-family: "Playfair Display", Georgia, serif; font-weight: 400;
    font-size: 53px; line-height: 1.1;
  }
  .hero-divider { margin: 14px auto 0; display: block; }
  .hero-tagline {
    margin-top: 18px; font-family: "Playfair Display", Georgia, serif;
    font-size: 17px; letter-spacing: 3.4px; color: var(--soft-white);
  }
  .info-bar {
    position: absolute; left: 0; right: 0; bottom: 0; height: 53px;
    background: var(--bar); display: flex; align-items: center;
    justify-content: space-between; padding: 0 14px; font-size: 11.5px; color: var(--soft-white);
  }
  .info-list { display: flex; gap: 18px; list-style: none; }
  .info-item { display: flex; align-items: center; gap: 6px; }
  .copyright { font-weight: 700; color: var(--ink-white); }
</style>
</head>
<body>
<main class="hero">
  <div class="hero-photo" role="img" aria-label="Photograph of a guest reading a menu at a candlelit bistro table with glasses and a red flower"></div>

  <nav class="social-links" aria-label="Social media">
    <span>Kindlepost</span>
    <span>Chirpline</span>
    <span>Pinboardly</span>
    <span>Linkward</span>
    <span>Orbit+</span>
    <svg width="15" height="11" viewBox="0 0 15 11" aria-label="Email">
      <rect x="0" y="0" width="15" height="11" rx="1.5" fill="#ffffff"/>
      <path d="M0.8 1 L7.5 6 L14.2 1" fill="none" stroke="#140d0c" stroke-width="1.3"/>
    </svg>
  </nav>

  <header class="brand-banner">
    <svg width="172" height="181" viewBox="0 0 172 181" aria-hidden="true">
      <path d="M0 0 H172 V150 L86 181 L0 150 Z" fill="#ffffff"/>
    </svg>
    <div class="brand-name">Serata Bistro</div>
  </header>

  <div class="menu-toggle" aria-label="Open menu"><i></i><i></i><i></i></div>

  <section class="hero-copy">
    <h1 class="hero-title">Welcome to the Serata Bistro</h1>
    <svg class="hero-divider" width="190" height="26" viewBox="0 0 190 26" aria-hidden="true">
      <line x1="0" y1="17" x2="72" y2="17" stroke="#ffffff" stroke-width="1"/>
      <line x1="118" y1="17" x2="190" y2="17" stroke="#ffffff" stroke-width="1"/>
      <path d="M82 21 A13 13 0 0 1 108 21 Z" fill="#ffffff"/>
      <rect x="79" y="21" width="32" height="2" fill="#ffffff"/>
      <circle cx="95" cy="6" r="1.8" fill="#ffffff"/>
    </svg>
    <p class="hero-tagline">ITALIAN CUISINE &amp; WINE BAR</p>
  </section>

  <footer class="info-bar">
    <ul class="info-list">
      <li class="info-item">
        <svg width="11" height="11" viewBox="0 0 24 24" aria-hidden="true"><path fill="#d4202b" d="M6.6 10.8a15.1 15.1 0 0 0 6.6 6.6l2.2-2.2a1 1 0 0 1 1-.25 11.4 11.4 0 0 0 3.6.57 1 1 0 0 1 1 1V20a1 1 0 0 1-1 1A17 17 0 0 1 3 4a1 1 0 0 1 1-1h3.5a1 1 0 0 1 1 1c0 1.250.2 2.450.57 3.570a1 1 0 0 1-.25 1z"/></svg>
        555 0142
      </li>
      <li class="info-item">
        <svg width="9" height="13" viewBox="0 0 12 18" aria-hidden="true"><path fill="#d4202b" d="M6 0a6 6 0 0 0-6 6c0 4.5 6 12 6 12s6-7.5 6-12a6 6 0 0 0-6-6zm0 8.2A2.2 2.2 0 1 1 6 3.8a2.2 2.2 0 0 1 0 4.4z"/></svg>
        Calle Olmo 12, Centro, Puerto Ventana
      </li>
      <li class="info-item">
        <svg width="12" height="12" viewBox="0 0 24 24" aria-hidden="true"><circle cx="12" cy="12" r="10" fill="none" stroke="#d4202b" stroke-width="2.6"/><path d="M12 6v6h4" fill="none" stroke="#d4202b" stroke-width="2.4"/></svg>
        Open daily from 5 to 12 am
      </li>
    </ul>
    <p class="copyright">© 2017 Seratabistro.example. All rights reserved.</p>
  </footer>
</main>
</body>
</html>
```